PowerPoint template for a tech startup

We need a PowerPoint template with a title slide, text slide, section slide, and thank you slide.
Our application helps engineering teams to be more productive. We would love a design that is slick, sophisticated, and consistent with our brand. (see more at www.velmo.ai or attached files)
By the way (not a requirement), Velmo means lighthouse in Greek.
Also, here is the font we used (not required) - https://glyphvault.net/fonts/league-gothic

• https://glyphvault.net/fonts/league-gothic

```html
<!DOCTYPE html>
<html lang="en">
<head>
<meta charset="utf-8">
<title>Velmo Presentation Template</title>
<link href="https://fonts.googleapis.com/css2?family=Poppins:ital,wght@0,400;0,500;0,600;0,700;1,400;1,500&display=swap" rel="stylesheet">
<style>
:root{
  --navy:#1c5378;
  --navy-dark:#174463;
  --orange:#e8631c;
  --peach:#d4855a;
  --black:#0f0f10;
  --ink:#2b2b2b;
  --muted:#6b6b6b;
  --bar:#2c2c2e;
  --paper:#ffffff;
}
*{box-sizing:border-box;margin:0;padding:0}
html,body{width:1143px;height:1200px;overflow:hidden;background:var(--paper)}
body{position:relative;font-family:'Poppins',sans-serif;color:var(--ink)}
.slide{position:absolute;width:305px;height:172px;background:var(--paper);overflow:hidden;box-shadow:4px 5px 12px rgba(0,0,0,.28)}
.col1{left:45px}.col2{left:419px}.col3{left:792px}
.row1{top:72px}.row2{top:294px}.row3{top:516px}.row4{top:738px}.row5{top:960px}
.abs{position:absolute}
.brand{position:absolute;left:18px;top:8px;font-weight:600;font-size:7px;color:var(--navy);letter-spacing:.2px}
.brand.light{color:#fff}
.footer{position:absolute;left:0;right:0;bottom:0;height:8px;background:var(--bar);color:#bdbdbd;font-size:3px;line-height:8px}
.footer .url{position:absolute;left:23px}
.footer .num{position:absolute;right:24px}
.photo{position:absolute}
.ph-office{background:linear-gradient(135deg,#d8c9b8,#8a7b6b 55%,#c7a57d)}
.ph-city{background:linear-gradient(135deg,#c9c7dd,#7d7fa6 50%,#e2d7cf)}
.ph-keys{background:linear-gradient(160deg,#3a4450,#8b8f92 55%,#6e5a47)}
.ph-man{background:linear-gradient(135deg,#6d5a4a,#3c4a66 55%,#a9a3a0)}
.ph-head{background:linear-gradient(160deg,#8d7464,#c9a790 60%,#6b5d55)}
.title{font-weight:600;line-height:1.12;color:var(--navy)}
.title .hl{color:var(--orange)}
.body{font-size:2.7px;line-height:1.55;color:var(--muted);text-align:justify}
.body.light{color:#a9a9a9}
.big{font-weight:600;color:var(--navy);line-height:1}
.big .hl{color:var(--orange)}
.item-title{font-size:3.2px;font-style:italic;font-weight:500;color:var(--navy)}
.item-title.light{color:#fff}
.center{text-align:center}
.icon{position:absolute;width:7px;height:7px}
.name{font-size:2.8px;font-weight:600;color:var(--navy);text-align:center}
.role{font-size:2px;color:var(--orange);text-align:center;font-style:italic}
</style>
</head>
<body>

<!-- 1 cover navy -->
<section class="slide col1 row1" style="background:var(--navy)">
  <div class="abs" style="left:50px;top:68px;font-weight:600;font-size:24px;color:#fff;line-height:1">Velmo</div>
  <div class="abs" style="left:52px;top:99px;width:68px;height:1px;background:#fff"></div>
  <div class="abs title" style="left:143px;top:66px;font-size:12.5px;color:#fff">Your Title<br>Presentation<br><span class="hl">Goes Here</span></div>
</section>

<!-- 2 cover peach -->
<section class="slide col2 row1" style="background:var(--peach)">
  <div class="abs" role="img" aria-label="Decorative network of connected dots" style="inset:0;background:radial-gradient(ellipse at 20% 20%,rgba(110,55,25,.35),transparent 55%),radial-gradient(ellipse at 90% 85%,rgba(110,55,25,.35),transparent 50%)"></div>
  <div class="abs" style="left:50px;top:68px;font-weight:600;font-size:24px;color:#fff;line-height:1">Velmo</div>
  <div class="abs" style="left:52px;top:99px;width:68px;height:1px;background:#fff"></div>
  <div class="abs title" style="left:145px;top:64px;font-size:12.5px;color:#fff">Your Title<br>Presentation<br>Goes Here</div>
</section>

<!-- 3 about -->
<section class="slide col3 row1" style="background:var(--black)">
  <div class="brand" style="color:var(--orange)">Velmo</div>
  <div class="abs big" style="left:17px;top:46px;font-size:14px;color:#fff">About <span class="hl">Us</span></div>
  <p class="abs body light" style="left:17px;top:73px;width:135px">Velmo helps engineering teams ship faster with clear insight into their daily work and delivery flow. Track progress, spot blockers early and keep every sprint moving toward the goals that matter most.</p>
  <div class="photo ph-man" role="img" aria-label="Young man working on a laptop outdoors" style="left:177px;top:9px;width:128px;height:155px"></div>
  <div class="footer"><span class="url">www.velmo.ai</span><span class="num">3</span></div>
</section>

<!-- 4 -->
<section class="slide col1 row2">
  <div class="brand">Velmo</div>
  <div class="photo ph-office" role="img" aria-label="Team working together at a table with laptops" style="left:0;top:30px;width:133px;height:134px"></div>
  <div class="abs title" style="left:149px;top:31px;font-size:12px">Your Title<br>Presentation<br><span class="hl">Goes Here</span></div>
  <p class="abs body" style="left:149px;top:87px;width:133px">Velmo helps engineering teams ship faster with clear insight into their daily work and delivery flow. Track progress, spot blockers early and keep every sprint moving toward the goals that matter most.</p>
  <div class="footer"><span class="url">www.velmo.ai</span><span class="num">4</span></div>
</section>

<!-- 5 -->
<section class="slide col2 row2">
  <div class="brand">Velmo</div>
  <div class="photo ph-city" role="img" aria-label="City skyline blended with hands typing" style="left:21px;top:22px;width:84px;height:68px"></div>
  <div class="photo ph-city" role="img" aria-label="Hands on a laptop over a city view" style="left:110px;top:22px;width:169px;height:68px"></div>
  <div class="abs title" style="left:21px;top:102px;font-size:11px">Your Title Slide<br><span class="hl">Goes Here</span></div>
  <p class="abs body" style="left:135px;top:104px;width:145px">Velmo helps engineering teams ship faster with clear insight into their daily work and delivery flow.</p>
  <div class="abs" style="left:135px;top:119px;width:80px;height:.5px;background:var(--orange)"></div>
  <p class="abs body" style="left:135px;top:126px;width:145px">Velmo helps engineering teams ship faster with clear insight into their daily work and delivery flow.</p>
  <div class="footer"><span class="url">www.velmo.ai</span><span class="num">5</span></div>
</section>

<!-- 6 -->
<section class="slide col3 row2">
  <div class="brand">Velmo</div>
  <div class="abs title" style="left:44px;top:33px;font-size:12px">Your Title<br>Slide<br><span class="hl">Goes Here</span></div>
  <p class="abs body" style="left:132px;top:36px;width:140px">Velmo helps engineering teams ship faster with clear insight into their daily work and delivery flow. Track progress, spot blockers early and keep every sprint moving toward the goals that matter most.</p>
  <div class="photo ph-man" role="img" aria-label="Man with a laptop" style="left:42px;top:93px;width:64px;height:60px"></div>
  <div class="photo ph-office" role="img" aria-label="Team meeting at a table" style="left:120px;top:93px;width:64px;height:60px"></div>
  <div class="photo ph-city" role="img" aria-label="City view blended with laptop work" style="left:198px;top:93px;width:107px;height:60px"></div>
  <div class="footer"><span class="url">www.velmo.ai</span><span class="num">6</span></div>
</section>

<!-- 7 vision -->
<section class="slide col1 row3">
  <div class="brand">Velmo</div>
  <div class="photo ph-keys" role="img" aria-label="Hands typing on a keyboard" style="left:43px;top:25px;width:262px;height:61px"></div>
  <div class="abs" style="left:24px;top:99px;width:164px;height:.8px;background:#cfcfcf"></div>
  <div class="abs" style="left:106px;top:99px;width:82px;height:.8px;background:var(--orange)"></div>
  <div class="abs big" style="left:22px;top:107px;font-size:20px">Our <span class="hl">vision</span></div>
  <div class="abs" style="left:148px;top:110px;font-size:3px;font-style:italic">01</div>
  <p class="abs body" style="left:155px;top:109px;width:45px">Short note about this item goes here.</p>
  <div class="abs" style="left:148px;top:133px;font-size:3px;font-style:italic">02</div>
  <p class="abs body" style="left:155px;top:132px;width:45px">Short note about this item goes here.</p>
  <div class="abs" style="left:224px;top:110px;font-size:3px;font-style:italic">03</div>
  <p class="abs body" style="left:231px;top:109px;width:45px">Short note about this item goes here.</p>
  <div class="abs" style="left:224px;top:133px;font-size:3px;font-style:italic">04</div>
  <p class="abs body" style="left:231px;top:132px;width:45px">Short note about this item goes here.</p>
  <div class="footer"><span class="url">www.velmo.ai</span><span class="num">7</span></div>
</section>

<!-- 8 service dark -->
<section class="slide col2 row3" style="background:linear-gradient(135deg,#1b1b1c,#070707)">
  <div class="brand" style="color:var(--navy)">Velmo</div>
  <div class="abs big" style="left:23px;top:33px;font-size:19px;color:#fff">Our <span class="hl">service</span></div>
  <p class="abs" style="left:24px;top:61px;width:122px;font-size:4.6px;font-style:italic;color:#ddd;line-height:1.55">“ Clear signals help teams focus on the work that truly counts.</p>
  <div class="photo ph-city" role="img" aria-label="City skyline blended with laptop work" style="left:25px;top:102px;width:115px;height:47px"></div>
  <svg class="icon" style="left:180px;top:37px" viewBox="0 0 10 10"><rect x="2" y="1" width="6" height="3" fill="var(--orange)"/><circle cx="3" cy="7" r="1.5" fill="var(--orange)"/><circle cx="7" cy="7" r="1.5" fill="var(--orange)"/></svg>
  <div class="abs item-title light center" style="left:150px;top:46px;width:68px">Text Tittle Here</div>
  <p class="abs body light center" style="left:155px;top:52px;width:58px">Short note about this item goes here.</p>
  <svg class="icon" style="left:259px;top:37px" viewBox="0 0 10 10"><rect x="2" y="1" width="6" height="3" fill="var(--orange)"/><circle cx="3" cy="7" r="1.5" fill="var(--orange)"/><circle cx="7" cy="7" r="1.5" fill="var(--orange)"/></svg>
  <div class="abs item-title light center" style="left:229px;top:46px;width:68px">Text Tittle Here</div>
  <p class="abs body light center" style="left:234px;top:52px;width:58px">Short note about this item goes here.</p>
  <svg class="icon" style="left:180px;top:91px" viewBox="0 0 10 10"><rect x="1" y="3" width="6" height="4" fill="var(--orange)"/><rect x="7" y="4.5" width="2.5" height="2.5" fill="var(--orange)"/><circle cx="3" cy="8" r="1" fill="var(--orange)"/><circle cx="8" cy="8" r="1" fill="var(--orange)"/></svg>
  <div class="abs item-title light center" style="left:150px;top:101px;width:68px">Text Tittle Here</div>
  <p class="abs body light center" style="left:155px;top:107px;width:58px">Short note about this item goes here.</p>
  <svg class="icon" style="left:259px;top:91px" viewBox="0 0 10 10"><path d="M1 5 L4 2 L6 4 L9 2 L9 6 L5 9 Z" fill="var(--orange)"/></svg>
  <div class="abs item-title light center" style="left:229px;top:101px;width:68px">Text Tittle Here</div>
  <p class="abs body light center" style="left:234px;top:107px;width:58px">Short note about this item goes here.</p>
  <div class="footer"><span class="url">www.velmo.ai</span><span class="num">8</span></div>
</section>

<!-- 9 -->
<section class="slide col3 row3">
  <div class="brand">Velmo</div>
  <div class="photo ph-keys" role="img" aria-label="Hands typing on a keyboard" style="left:20px;top:26px;width:75px;height:69px"></div>
  <div class="photo ph-office" role="img" aria-label="Colleagues discussing around laptops" style="left:110px;top:26px;width:170px;height:69px"></div>
  <div class="abs title center" style="left:20px;top:98px;width:260px;font-size:11px">Your Title <span class="hl">Slide Goes Here</span></div>
  <p class="abs body" style="left:26px;top:115px;width:68px">Velmo helps engineering teams ship faster with clear insight into their daily work and delivery flow.</p>
  <p class="abs body" style="left:113px;top:115px;width:164px">Velmo helps engineering teams ship faster with clear insight into their daily work and delivery flow. Track progress, spot blockers early and keep every sprint moving toward the goals that matter most.</p>
  <div class="footer"><span class="url">www.velmo.ai</span><span class="num">9</span></div>
</section>

<!-- 10 -->
<section class="slide col1 row4">
  <div class="brand">Velmo</div>
  <div class="abs" style="right:6px;top:16px;font-size:2.2px;font-weight:600">Modern Style</div>
  <div class="abs title" style="left:24px;top:22px;font-size:12px">Your Title<br><span class="hl">Slide Goes<br>Here</span></div>
  <p class="abs body" style="left:24px;top:78px;width:75px">Velmo helps engineering teams ship faster with clear insight into their daily work and delivery flow. Track progress, spot blockers early and keep every sprint moving toward the goals that matter most.</p>
  <p class="abs body" style="left:124px;top:45px;width:48px">Velmo helps engineering teams ship faster with clear insight into their daily work and delivery flow.</p>
  <p class="abs body" style="left:124px;top:115px;width:48px">Velmo helps engineering teams ship faster with clear insight into their daily work and delivery flow.</p>
  <div class="photo ph-man" role="img" aria-label="Man smiling at his laptop" style="left:183px;top:22px;width:103px;height:56px"></div>
  <div class="photo ph-keys" role="img" aria-label="Hands typing on a keyboard" style="left:183px;top:92px;width:103px;height:56px"></div>
  <div class="footer"><span class="url">www.velmo.ai</span><span class="num">10</span></div>
</section>

<!-- 11 team -->
<section class="slide col2 row4">
  <div class="brand">Velmo</div>
  <div class="abs big center" style="left:0;top:12px;width:305px;font-size:12px;color:var(--navy)">Our <span class="hl">team</span></div>
  <div class="photo ph-head" role="img" aria-label="Team member portrait" style="left:17px;top:36px;width:66px;height:50px"></div>
  <div class="photo ph-head" role="img" aria-label="Team member portrait" style="left:116px;top:36px;width:66px;height:50px"></div>
  <div class="photo ph-head" role="img" aria-label="Team member portrait" style="left:216px;top:36px;width:66px;height:50px"></div>
  <div class="abs" style="left:17px;top:87px;width:66px"><div class="name">John Doe Bagus</div><div class="role">Job Position</div></div>
  <div class="abs" style="left:116px;top:87px;width:66px"><div class="name">John Doe Bagus</div><div class="role">Job Position</div></div>
  <div class="abs" style="left:216px;top:87px;width:66px"><div class="name">John Doe Bagus</div><div class="role">Job Position</div></div>
  <div class="photo ph-head" role="img" aria-label="Team member portrait" style="left:17px;top:99px;width:66px;height:51px"></div>
  <div class="photo ph-head" role="img" aria-label="Team member portrait" style="left:116px;top:99px;width:66px;height:51px"></div>
  <div class="photo ph-head" role="img" aria-label="Team member portrait" style="left:216px;top:99px;width:66px;height:51px"></div>
  <div class="abs" style="left:17px;top:151px;width:66px"><div class="name">John Doe Bagus</div><div class="role">Job Position</div></div>
  <div class="abs" style="left:116px;top:151px;width:66px"><div class="name">John Doe Bagus</div><div class="role">Job Position</div></div>
  <div class="abs" style="left:216px;top:151px;width:66px"><div class="name">John Doe Bagus</div><div class="role">Job Position</div></div>
  <div class="footer"><span class="url">www.velmo.ai</span><span class="num">11</span></div>
</section>

<!-- 12 service -->
<section class="slide col3 row4">
  <div class="brand">Velmo</div>
  <div class="photo ph-city" role="img" aria-label="City skyline blended with laptop work" style="left:28px;top:40px;width:117px;height:61px"></div>
  <div class="abs big" style="left:163px;top:35px;font-size:20px">Our <span class="hl">service</span></div>
  <p class="abs body" style="left:164px;top:60px;width:122px">Velmo helps engineering teams ship faster with clear insight into their daily work and delivery flow. Track progress, spot blockers early and keep every sprint moving toward the goals that matter most.</p>
  <svg class="icon" style="left:59px;top:112px" viewBox="0 0 10 10"><circle cx="5" cy="4" r="2" fill="var(--orange)"/><circle cx="2" cy="5" r="1.3" fill="var(--orange)"/><circle cx="8" cy="5" r="1.3" fill="var(--orange)"/><rect x="2" y="7" width="6" height="2" fill="var(--orange)"/></svg>
  <div class="abs item-title center" style="left:27px;top:121px;width:70px">Text Tittle Here</div>
  <p class="abs body center" style="left:27px;top:127px;width:70px">Short note about this item goes here.</p>
  <svg class="icon" style="left:152px;top:112px" viewBox="0 0 10 10"><rect x="1" y="1" width="8" height="8" fill="none" stroke="var(--orange)" stroke-width="1"/><rect x="3" y="5" width="1" height="3" fill="var(--orange)"/><rect x="5" y="3" width="1" height="5" fill="var(--orange)"/><rect x="7" y="4" width="1" height="4" fill="var(--orange)"/></svg>
  <div class="abs item-title center" style="left:120px;top:121px;width:70px">Text Tittle Here</div>
  <p class="abs body center" style="left:120px;top:127px;width:70px">Short note about this item goes here.</p>
  <svg class="icon" style="left:245px;top:112px" viewBox="0 0 10 10"><circle cx="5" cy="5" r="4" fill="none" stroke="var(--orange)" stroke-width="1"/><circle cx="5" cy="5" r="1.6" fill="var(--orange)"/></svg>
  <div class="abs item-title center" style="left:213px;top:121px;width:70px">Text Tittle Here</div>
  <p class="abs body center" style="left:213px;top:127px;width:70px">Short note about this item goes here.</p>
  <div class="footer"><span class="url">www.velmo.ai</span><span class="num">12</span></div>
</section>

<!-- 13 service centered -->
<section class="slide col1 row5">
  <div class="brand">Velmo</div>
  <div class="abs big center" style="left:0;top:23px;width:305px;font-size:20px">Our <span class="hl">service</span></div>
  <p class="abs body center" style="left:45px;top:49px;width:215px">Velmo helps engineering teams ship faster with clear insight into their daily work and delivery flow. Track progress, spot blockers early and keep every sprint moving toward the goals that matter most. Velmo helps engineering teams ship faster with clear insight into their daily work and delivery flow.</p>
  <svg class="icon" style="left:57px;top:93px;width:9px;height:9px" viewBox="0 0 10 10"><rect x="1" y="2" width="8" height="5" fill="none" stroke="var(--orange)" stroke-width="1"/><rect x="3" y="8" width="4" height="1" fill="var(--orange)"/></svg>
  <div class="abs" style="left:139px;top:86px;width:28px;height:28px;border-radius:50%;background:#e6e6e6"></div>
  <svg class="icon" style="left:148px;top:95px;width:10px;height:10px" viewBox="0 0 10 10"><rect x="1" y="2" width="8" height="6" fill="none" stroke="var(--orange)" stroke-width="1"/><circle cx="5" cy="5" r="1.5" fill="var(--orange)"/></svg>
  <svg class="icon" style="left:242px;top:93px;width:9px;height:9px" viewBox="0 0 10 10"><circle cx="5" cy="4" r="3" fill="none" stroke="var(--orange)" stroke-width="1"/><rect x="4" y="7" width="2" height="2" fill="var(--orange)"/></svg>
  <div class="abs item-title center" style="left:26px;top:120px;width:70px">Text Tittle Here</div>
  <p class="abs body center" style="left:26px;top:126px;width:70px">Short note about this item goes here.</p>
  <div class="abs item-title center" style="left:118px;top:120px;width:70px">Text Tittle Here</div>
  <p class="abs body center" style="left:118px;top:126px;width:70px">Short note about this item goes here.</p>
  <div class="abs item-title center" style="left:211px;top:120px;width:70px">Text Tittle Here</div>
  <p class="abs body center" style="left:211px;top:126px;width:70px">Short note about this item goes here.</p>
  <div class="footer"><span class="url">www.velmo.ai</span><span class="num">13</span></div>
</section>

<!-- 14 service with photo -->
<section class="slide col2 row5">
  <div class="brand">Velmo</div>
  <div class="photo ph-keys" role="img" aria-label="Hands typing on a keyboard at a desk" style="left:164px;top:9px;width:141px;height:155px"></div>
  <div class="abs" style="left:281px;top:16px;font-size:2.2px;font-weight:600;color:#fff">Modern Style</div>
  <div class="abs big" style="left:26px;top:21px;font-size:20px">Our <span class="hl">service</span></div>
  <p class="abs body" style="left:28px;top:47px;width:118px">Velmo helps engineering teams ship faster with clear insight into their daily work and delivery flow.</p>
  <svg class="icon" style="left:32px;top:72px" viewBox="0 0 10 10"><circle cx="5" cy="5" r="3" fill="none" stroke="var(--orange)" stroke-width="1.6" stroke-dasharray="1.5 1"/></svg>
  <div class="abs item-title" style="left:52px;top:69px">Text Tittle Here</div>
  <p class="abs body" style="left:52px;top:75px;width:88px">Velmo helps engineering teams ship faster with clear insight into their daily work and delivery flow.</p>
  <svg class="icon" style="left:32px;top:102px" viewBox="0 0 10 10"><circle cx="5" cy="5" r="2" fill="var(--orange)"/><circle cx="5" cy="5" r="4" fill="none" stroke="var(--orange)" stroke-width=".6" stroke-dasharray="1 1"/></svg>
  <div class="abs item-title" style="left:52px;top:99px">Text Tittle Here</div>
  <p class="abs body" style="left:52px;top:105px;width:88px">Velmo helps engineering teams ship faster with clear insight into their daily work and delivery flow.</p>
  <svg class="icon" style="left:32px;top:132px" viewBox="0 0 10 10"><path d="M5 1 L9 2.5 L8.5 6 L5 9 L1.5 6 L1 2.5 Z" fill="var(--orange)"/></svg>
  <div class="abs item-title" style="left:52px;top:129px">Text Tittle Here</div>
  <p class="abs body" style="left:52px;top:135px;width:88px">Velmo helps engineering teams ship faster with clear insight into their daily work and delivery flow.</p>
  <div class="footer"><span class="url">www.velmo.ai</span><span class="num">14</span></div>
</section>

<!-- 15 -->
<section class="slide col3 row5">
  <div class="brand">Velmo</div>
  <div class="abs title" style="left:24px;top:37px;font-size:12px">Your Title<br><span class="hl">Slide Goes<br>Here</span></div>
  <div class="abs" style="left:103px;top:32px;font-size:4.4px;font-weight:600;color:var(--navy)">Your SubTitle Goes Here</div>
  <p class="abs body" style="left:103px;top:40px;width:112px">Velmo helps engineering teams ship faster with clear insight into their daily work and delivery flow. Track progress, spot blockers early and keep every sprint moving toward the goals that matter most.</p>
  <div class="photo ph-man" role="img" aria-label="Man working on a laptop" style="left:225px;top:30px;width:58px;height:59px"></div>
  <div class="photo ph-city" role="img" aria-label="City view blended with laptop work" style="left:21px;top:92px;width:100px;height:60px"></div>
  <div class="abs" style="left:132px;top:94px;font-size:4.4px;font-weight:600;color:var(--navy)">Your SubTitle Goes Here</div>
  <p class="abs body" style="left:132px;top:102px;width:151px">Velmo helps engineering teams ship faster with clear insight into their daily work and delivery flow. Track progress, spot blockers early and keep every sprint moving toward the goals that matter most. Velmo helps engineering teams ship faster with clear insight into their daily work and delivery flow.</p>
  <div class="footer"><span class="url">www.velmo.ai</span><span class="num">15</span></div>
</section>

</body>
</html>
```